IT consulting company looking for a modern business design for a website and a new logo

We are the IT-consulting company VelmaTrix from Germany and need a new and modern business website and a new logo. We are specialized in output management. Our services include business analysis, outsourcing, development, training and project leading. We wish for a design with nature pictures (mountains, lakes, rivers, forests, etc.) for our company with the colors green and blue. If it is possible, a slow-mo video of a nature scene. The design should be responsive and the menu should change to a hamburger menu. The following are: • Services / Solutions 1. Output Management 2. Outsourcing 3. Development 4. Business Analyst 5. Training • Partners • Careers • About Us 1. Project A 2. Project B 3. Project C • Contact Notes for the following categories: For "Services / Solutions" we want to conclude some contents from all the sub-points and sub-points below. Additionally, we would like to see some sub-point under "Services / Solutions". For Output Management: "5 Benefits of Output Management Systems (OMS) - OMS Simplifies and Accelerates External Communication - Helps Reduce Communication Mistakes - Provides Customers With Fast and Secure Responses to your questions - Employees can focus on the essential as they can access prepared templates - Companies get complete transparency about their communication "The point" partner does not have sub-points. The content here is a quote and the logo from the company Brel. For now, just placeholders on this site. The next point wants to be "career" without sub-point and wants to contain some text. Carrer options wants to be listed here. Next point wants to be "About us", where we need sub-points which we do not know exactly at this moment, but they will contain text. By clicking directly on "About us" we want to include pictures and texts about 6 employees for which we only need placeholders at the moment. The last point wants to be "contact", where customers can send us messages. The main page should include a story about our company, which can be a placeholder for now. For reference, designs have a look at: https://brelvanto.de/ https://www.tarnopix.com/ https://www.pldrive.de/ We prefer WordPress designs, created with the plugin ELEMENTOR, so that we can easily edit the content by ourselves. The final design should look professional, competent and modern.

Target Market(s)

With our website, we want to reach the following target groups. <br> <br> <br> <br> <br> <br> <br> <br> <br> <br> <br> <br> <br> <br> <br> <br> <br> <br> <br> <br> <br> <br> <br> <br> <br> <br> <br> <br> <br> <br> <br> <br> <br> <br> <br> <br> <br> <br> <br> <br> <br> <br> <br> <br> <br> <br> <br> <br> <br>

Industry/Entity Type

Consulting

Logo Text

(optionally) VelmaTrix

Font styles to use
Sans Serif

Colors

Designer to choose colors to be used in the design.

Requirements
Must have
• 1. Outsourcing 3. Development 4. Business Analyst 5. Training • Partners • Careers • About Us 1. Project A 2. Project B 3. Project C • Contact The above-mentioned background picture with nature motifs (mountains, lakes, rivers, forests, etc.). WordPress design in primary colors blue and green.
Nice to have
• ELEMENTOR template. Effects for the background pictures. Counter of all successful projects for Output Management, Business Analyst and Training

```html
<!DOCTYPE html>
<html lang="de">
<head>
<meta charset="utf-8">
<title>VelmaTrix – IT Consulting</title>
<link rel="stylesheet" href="https://fonts.googleapis.com/css2?family=Poppins:wght@400;500;600;700;800&family=Montserrat:wght@500;600&family=Open+Sans:wght@400;600;700&family=PT+Sans:wght@400;700&display=swap">
<style>
:root{
  --blue:#1f5fa8;
  --blue-dark:#17457d;
  --blue-panel:#235e9c;
  --blue-icon:#2f8ee0;
  --green:#6aad1b;
  --ink:#2b2b2b;
  --text:#444;
  --muted:#666;
  --grey-bg:#efefef;
  --warm-bg:#f4f0f0;
  --white:#fff;
}
*{box-sizing:border-box;margin:0;padding:0}
html,body{width:1200px;height:4264px;overflow:hidden}
body{position:relative;background:var(--white);font-family:"Open Sans",sans-serif;color:var(--text)}
.abs{position:absolute}
.btn{position:absolute;background:var(--green);color:var(--white);font-family:"Poppins",sans-serif;font-weight:700;display:flex;align-items:center;justify-content:center;letter-spacing:.3px;box-shadow:0 2px 4px rgba(0,0,0,.15)}
.section-title{position:absolute;left:0;width:1200px;text-align:center;font-family:"Poppins",sans-serif;font-weight:700;font-size:33px;color:var(--ink);letter-spacing:-.3px}

/* header + hero */
.hero{position:absolute;left:0;top:0;width:1200px;height:708px;background:linear-gradient(180deg,#ffffff 0%,#ffffff 11%,#c9d8ea 17%,#8fb0d6 26%,#5f86b9 40%,#3e5f92 58%,#2b3f63 75%,#23334f 100%)}
.logo{position:absolute;left:144px;top:30px;font-family:"Poppins",sans-serif;font-weight:700;font-size:34px;color:var(--blue)}
.nav{position:absolute;top:44px;right:146px;display:flex;gap:30px;font-family:"Montserrat",sans-serif;font-weight:600;font-size:13px;color:#222}
.hero-title{position:absolute;left:603px;top:324px;font-family:"Poppins",sans-serif;font-weight:700;font-size:53px;color:var(--white);text-shadow:0 2px 6px rgba(0,0,0,.35)}
.hero-sub{position:absolute;left:604px;top:394px;font-family:"Poppins",sans-serif;font-weight:600;font-size:23px;color:var(--white)}

/* services */
.services{position:absolute;left:0;top:708px;width:1200px;height:914px;background:linear-gradient(120deg,#e9e9e9 0%,#f6f6f6 35%,#e8e8e8 60%,#f5f5f5 100%)}
.svc{position:absolute;width:288px;height:345px;background:var(--white);box-shadow:0 2px 8px rgba(0,0,0,.06);text-align:center}
.svc svg{position:absolute;left:108px;top:32px}
.svc .rule{position:absolute;left:124px;top:136px;width:40px;height:2px;background:var(--blue-icon)}
.svc h3{position:absolute;left:0;top:152px;width:100%;font-family:"Poppins",sans-serif;font-weight:500;font-size:17px;color:var(--ink)}
.svc p{position:absolute;left:30px;top:190px;width:228px;font-size:14px;line-height:21px;color:#444}
.svc .btn{left:93px;top:274px;width:102px;height:31px;font-size:11px}
.svc-all{position:absolute;left:763px;top:499px;width:288px;height:345px;background:linear-gradient(180deg,#2d80cf 0%,#2a6fb5 45%,#1f5391 100%)}

/* welcome */
.welcome-photo{position:absolute;left:144px;top:1672px;width:511px;height:547px;background:linear-gradient(135deg,#3a3634 0%,#6b6460 40%,#cfcac4 55%,#3b3330 80%,#b0622d 100%)}
.welcome-card{position:absolute;left:576px;top:1726px;width:516px;height:455px;background:var(--white)}

/* careers */
.careers{position:absolute;left:0;top:2281px;width:1200px;height:691px;background:var(--warm-bg)}
.job{position:absolute;width:296px;height:247px;background:var(--white);font-family:"PT Sans",sans-serif}
.job svg{position:absolute;left:30px;top:27px}
.job h4{position:absolute;left:30px;top:106px;font-size:17px;font-weight:700;color:#333}
.job .date{position:absolute;left:30px;top:130px;font-size:12px;color:#666}
.job .meta{position:absolute;left:30px;top:160px;font-size:12px;color:#555;display:flex;align-items:center;gap:6px}
.job .btn{left:30px;top:195px;width:95px;height:26px;font-size:11px;box-shadow:none}

/* partners */
.partner{position:absolute;top:3130px;display:flex;align-items:center;gap:6px;font-family:"Poppins",sans-serif;font-weight:600;font-size:14px;color:var(--blue-dark)}
.partner i{display:block;width:18px;height:18px;background:var(--blue)}

/* contact */
.contact{position:absolute;left:0;top:3227px;width:1200px;height:637px;background:var(--warm-bg)}
.form-box{position:absolute;left:179px;top:3360px;width:504px;height:447px;background:var(--white)}
.field{position:absolute;font-size:12px;color:#444;border-bottom:1px solid #999;padding-bottom:8px}
.info-box{position:absolute;left:683px;top:3360px;width:338px;height:447px;background:var(--blue-panel);color:var(--white)}
.info-ic{position:absolute;left:47px;width:38px;height:38px;border-radius:50%;background:var(--blue-icon)}
.info-h{position:absolute;left:105px;font-family:"Poppins",sans-serif;font-weight:700;font-size:12px}
.info-t{position:absolute;left:105px;font-size:16px;line-height:23px}
.info-rule{position:absolute;left:32px;width:274px;height:1px;background:rgba(255,255,255,.3)}

/* footer */
.footer{position:absolute;left:0;top:3864px;width:1200px;height:400px;background:var(--blue)}
.f-h{position:absolute;top:50px;font-family:"Poppins",sans-serif;font-weight:600;font-size:11px;color:var(--white)}
.f-in{position:absolute;left:475px;width:228px;background:var(--white);font-size:10px;color:#555;padding:8px 10px}
.f-menu{position:absolute;left:775px;top:80px;font-size:10.5px;line-height:17.5px;color:var(--white);text-transform:uppercase}
.soc{position:absolute;left:960px;display:flex;align-items:center;gap:12px;font-size:11px;color:var(--white)}
.soc span{display:block;width:28px;height:28px;border-radius:50%;background:#1a4f93}
</style>
</head>
<body>

<!-- HERO -->
<section class="hero">
  <div class="abs" role="img" aria-label="Photo: hiker standing on a rocky summit facing snowy mountain ranges" style="left:0;top:110px;width:1200px;height:598px;background:radial-gradient(ellipse at 40% 10%,rgba(230,238,248,.55),rgba(0,0,0,0) 55%),linear-gradient(180deg,rgba(0,0,0,0) 55%,rgba(20,24,40,.45) 100%)"></div>
  <div class="logo">VelmaTrix</div>
  <nav class="nav"><span>HOME</span><span>SERVICES</span><span>PARTNER</span><span>KARRIERE</span><span>ÜBER UNS</span><span>KONTAKT</span></nav>
  <h1 class="hero-title">Business Analysis</h1>
  <p class="hero-sub">Lorem Ipsum is simply dummy text</p>
  <div class="btn" style="left:607px;top:457px;width:141px;height:50px;font-size:16px">READ MORE</div>
</section>

<!-- SERVICES -->
<section class="services">
  <h2 class="section-title" style="top:54px">OUR SERVICES</h2>

  <div class="svc" style="left:151px;top:139px">
    <svg width="72" height="84" viewBox="0 0 72 84" fill="#333"><circle cx="36" cy="9" r="7"/><rect x="27" y="17" width="18" height="14" rx="3"/><path d="M36 34v10M36 44L14 56M36 44l22 12" stroke="#333" stroke-width="3" fill="none"/><circle cx="36" cy="48" r="4"/><circle cx="12" cy="58" r="6"/><rect x="3" y="65" width="18" height="14" rx="3"/><circle cx="60" cy="58" r="6"/><rect x="51" y="65" width="18" height="14" rx="3"/><circle cx="36" cy="62" r="5"/><rect x="28" y="68" width="16" height="11" rx="3"/></svg>
    <div class="rule"></div><h3>Output Management</h3>
    <p>Lorem ipsum dolor sit amet consectetur adipiscing elit sed do eiusmod tempor.</p>
    <div class="btn">READ MORE</div>
  </div>
  <div class="svc" style="left:457px;top:139px">
    <svg width="80" height="76" viewBox="0 0 80 76" fill="#333"><rect x="18" y="2" width="44" height="36" rx="3" fill="none" stroke="#333" stroke-width="4"/><circle cx="40" cy="18" r="9" fill="none" stroke="#333" stroke-width="3"/><path d="M35 18l4 4 7-8" stroke="#333" stroke-width="3" fill="none"/><path d="M2 42h14l14 10 10 0 8 8-6 6-14-6H2z"/><path d="M78 42H64L50 52l-6 6 8 10 12-6h14z"/></svg>
    <div class="rule"></div><h3>Outsourcing</h3>
    <p>Lorem ipsum dolor sit amet consectetur adipiscing elit sed do eiusmod tempor.</p>
    <div class="btn">READ MORE</div>
  </div>
  <div class="svc" style="left:763px;top:139px">
    <svg width="76" height="76" viewBox="0 0 76 76" fill="#333"><path d="M30 4h12l2 8 7 3 7-4 8 8-4 7 3 7 8 2v12l-8 2-3 7 4 7-8 8-7-4-7 3-2 8H30l-2-8-7-3-7 4-8-8 4-7-3-7-8-2V30l8-2 3-7-4-7 8-8 7 4 7-3z"/><circle cx="36" cy="38" r="12" fill="#fff"/><path d="M44 46l22 22" stroke="#fff" stroke-width="12"/><path d="M44 46l22 22" stroke="#333" stroke-width="7"/></svg>
    <div class="rule"></div><h3>Entwicklung</h3>
    <p>Lorem ipsum dolor sit amet consectetur adipiscing elit sed do eiusmod tempor.</p>
    <div class="btn">READ MORE</div>
  </div>
  <div class="svc" style="left:151px;top:499px">
    <svg width="76" height="76" viewBox="0 0 76 76" fill="#333"><circle cx="12" cy="9" r="7"/><path d="M4 20h16v26h-4v26h-8V46H4z"/><rect x="24" y="6" width="48" height="38" fill="none" stroke="#333" stroke-width="4"/><rect x="34" y="28" width="6" height="12"/><rect x="44" y="22" width="6" height="18"/><rect x="54" y="14" width="6" height="26"/><path d="M48 44L36 72M48 44l12 28M48 44v26" stroke="#333" stroke-width="3"/></svg>
    <div class="rule"></div><h3>Business Analyst</h3>
    <p>Lorem ipsum dolor sit amet consectetur adipiscing elit sed do eiusmod tempor.</p>
    <div class="btn">READ MORE</div>
  </div>
  <div class="svc" style="left:457px;top:499px">
    <svg width="72" height="76" viewBox="0 0 72 76" fill="#333"><rect x="14" y="2" width="44" height="34" fill="none" stroke="#333" stroke-width="4"/><circle cx="36" cy="14" r="5"/><path d="M28 30c0-7 16-7 16 0z"/><circle cx="14" cy="48" r="6"/><circle cx="36" cy="48" r="6"/><circle cx="58" cy="48" r="6"/><rect x="5" y="57" width="18" height="15" rx="4"/><rect x="27" y="57" width="18" height="15" rx="4"/><rect x="49" y="57" width="18" height="15" rx="4"/></svg>
    <div class="rule"></div><h3>Schulungen</h3>
    <p>Lorem ipsum dolor sit amet consectetur adipiscing elit sed do eiusmod tempor.</p>
    <div class="btn">READ MORE</div>
  </div>
  <div class="svc-all" role="img" aria-label="Photo: blue mountain lake landscape">
    <div class="btn" style="left:45px;top:155px;width:202px;height:42px;font-size:16px">VIEW ALL SERVICES</div>
  </div>
</section>

<!-- WELCOME -->
<section>
  <div class="welcome-photo" role="img" aria-label="Photo: hands holding a tablet showing business charts next to a coffee cup"></div>
  <div class="welcome-card">
    <p class="abs" style="left:43px;top:34px;font-family:'Poppins',sans-serif;font-weight:500;font-size:22px;color:var(--ink)">Welcome to</p>
    <h2 class="abs" style="left:37px;top:62px;font-family:'Poppins',sans-serif;font-weight:700;font-size:41px;color:var(--ink)">VelmaTrix</h2>
    <div class="abs" style="left:45px;top:125px;width:26px;height:3px;background:var(--blue)"></div>
    <div class="abs" style="left:76px;top:125px;width:18px;height:3px;background:var(--blue)"></div>
    <p class="abs" style="left:45px;top:160px;width:440px;font-size:17px;line-height:26px;color:#333">Led ut perspiciatis unde omnis iste natus error sit voluptatem accusantium doloremque.</p>
    <p class="abs" style="left:45px;top:236px;width:450px;font-size:14.5px;line-height:23.5px;color:#444">At vero eos et accusamus et iusto odio dignissimos ducimus qui blanditiis praesentium voluptatum deleniti atque corrupti quos dolores et quas molestias excepturi sint occaecati cupiditate non provident, similique sunt in culpa qui officia deserunt mollitia animi, id est laborum et dolorum fuga</p>
    <div class="btn" style="left:46px;top:384px;width:124px;height:39px;font-size:14px">READ MORE</div>
  </div>
</section>

<!-- CAREERS -->
<section class="careers">
  <h2 class="section-title" style="top:48px">KARRIERE</h2>
</section>
<div class="job" style="left:144px;top:2411px">
  <svg width="60" height="60" viewBox="0 0 60 60" fill="none" stroke="#1f6fc2" stroke-width="2"><circle cx="10" cy="8" r="5"/><path d="M4 18h12v18H4zM7 36v20M13 36v20"/><rect x="20" y="4" width="36" height="28"/><path d="M27 26v-6M34 26V14M41 26v-9M48 26V10M38 32L28 58M38 32l10 26M38 32v24"/></svg>
  <h4>Business Analyst</h4><p class="date">Posted on September 10, 2018</p>
  <div class="meta"><svg width="9" height="12" viewBox="0 0 9 12"><path d="M4.5 0A4.5 4.5 0 0 0 0 4.5C0 8 4.5 12 4.5 12S9 8 9 4.5A4.5 4.5 0 0 0 4.5 0z" fill="#777"/></svg>Hallstead, LV &nbsp;&nbsp;|&nbsp;&nbsp;<svg width="11" height="11" viewBox="0 0 11 11" fill="none" stroke="#777"><circle cx="5.5" cy="5.5" r="4.8"/><path d="M5.5 2.5v3h2"/></svg>Full/Part-time</div>
  <div class="btn">APPLY NOW</div>
</div>
<div class="job" style="left:452px;top:2411px">
  <svg width="60" height="60" viewBox="0 0 60 60" fill="none" stroke="#1f6fc2" stroke-width="2"><circle cx="24" cy="22" r="10"/><path d="M6 58c0-14 8-20 18-20s18 6 18 20M20 38l4 10 4-10"/><circle cx="46" cy="14" r="8"/><circle cx="46" cy="14" r="3"/><path d="M46 2v4M46 22v4M34 14h4M54 14h4"/></svg>
  <h4>Project Manager</h4><p class="date">Posted on September 10, 2018</p>
  <div class="meta"><svg width="9" height="12" viewBox="0 0 9 12"><path d="M4.5 0A4.5 4.5 0 0 0 0 4.5C0 8 4.5 12 4.5 12S9 8 9 4.5A4.5 4.5 0 0 0 4.5 0z" fill="#777"/></svg>Hallstead, LV &nbsp;&nbsp;|&nbsp;&nbsp;<svg width="11" height="11" viewBox="0 0 11 11" fill="none" stroke="#777"><circle cx="5.5" cy="5.5" r="4.8"/><path d="M5.5 2.5v3h2"/></svg>Full/Part-time</div>
  <div class="btn">APPLY NOW</div>
</div>
<div class="job" style="left:760px;top:2411px">
  <svg width="60" height="60" viewBox="0 0 60 60" fill="none" stroke="#1f6fc2" stroke-width="2"><rect x="4" y="4" width="44" height="32" rx="2"/><path d="M20 16l-6 5 6 5M32 16l6 5-6 5M28 14l-4 14M18 36v6M34 36v6M6 42h40v10H6z"/><circle cx="52" cy="48" r="5"/></svg>
  <h4>Software Engineer</h4><p class="date">Posted on September 10, 2018</p>
  <div class="meta"><svg width="9" height="12" viewBox="0 0 9 12"><path d="M4.5 0A4.5 4.5 0 0 0 0 4.5C0 8 4.5 12 4.5 12S9 8 9 4.5A4.5 4.5 0 0 0 4.5 0z" fill="#777"/></svg>Hallstead, LV &nbsp;&nbsp;|&nbsp;&nbsp;<svg width="11" height="11" viewBox="0 0 11 11" fill="none" stroke="#777"><circle cx="5.5" cy="5.5" r="4.8"/><path d="M5.5 2.5v3h2"/></svg>Full/Part-time</div>
  <div class="btn">APPLY NOW</div>
</div>
<div class="job" style="left:144px;top:2670px">
  <svg width="60" height="60" viewBox="0 0 60 60" fill="none" stroke="#1f6fc2" stroke-width="2"><rect x="16" y="26" width="28" height="22" rx="2"/><path d="M22 26v-6a8 8 0 0 1 16 0v6"/><circle cx="30" cy="36" r="3"/><path d="M30 39v4M4 20h10M4 50h10M46 20h10M46 50h10M4 35h8M48 35h8"/><circle cx="4" cy="20" r="2"/><circle cx="56" cy="50" r="2"/></svg>
  <h4>IT Security</h4><p class="date">Posted on September 10, 2018</p>
  <div class="meta"><svg width="9" height="12" viewBox="0 0 9 12"><path d="M4.5 0A4.5 4.5 0 0 0 0 4.5C0 8 4.5 12 4.5 12S9 8 9 4.5A4.5 4.5 0 0 0 4.5 0z" fill="#777"/></svg>Hallstead, LV &nbsp;&nbsp;|&nbsp;&nbsp;<svg width="11" height="11" viewBox="0 0 11 11" fill="none" stroke="#777"><circle cx="5.5" cy="5.5" r="4.8"/><path d="M5.5 2.5v3h2"/></svg>Full/Part-time</div>
  <div class="btn">APPLY NOW</div>
</div>
<div class="job" style="left:452px;top:2670px">
  <svg width="60" height="60" viewBox="0 0 60 60" fill="none" stroke="#1f6fc2" stroke-width="2"><rect x="2" y="2" width="16" height="12"/><rect x="42" y="2" width="16" height="12"/><rect x="2" y="44" width="16" height="12"/><rect x="42" y="44" width="16" height="12"/><circle cx="30" cy="29" r="10"/><path d="M20 29h20M30 19v20M18 10l6 10M42 10l-6 10M18 48l6-10M42 48l-6-10"/></svg>
  <h4>Data Scientist</h4><p class="date">Posted on September 10, 2018</p>
  <div class="meta"><svg width="9" height="12" viewBox="0 0 9 12"><path d="M4.5 0A4.5 4.5 0 0 0 0 4.5C0 8 4.5 12 4.5 12S9 8 9 4.5A4.5 4.5 0 0 0 4.5 0z" fill="#777"/></svg>Hallstead, LV &nbsp;&nbsp;|&nbsp;&nbsp;<svg width="11" height="11" viewBox="0 0 11 11" fill="none" stroke="#777"><circle cx="5.5" cy="5.5" r="4.8"/><path d="M5.5 2.5v3h2"/></svg>Full/Part-time</div>
  <div class="btn">APPLY NOW</div>
</div>
<div class="job" style="left:760px;top:2670px">
  <svg width="60" height="60" viewBox="0 0 60 60" fill="none" stroke="#1f6fc2" stroke-width="2.5"><rect x="4" y="4" width="52" height="52" rx="6"/><path d="M4 16h52M24 28l-8 8 8 8M36 28l8 8-8 8M32 26l-4 20"/></svg>
  <h4>Program Manager</h4><p class="date">Posted on September 10, 2018</p>
  <div class="meta"><svg width="9" height="12" viewBox="0 0 9 12"><path d="M4.5 0A4.5 4.5 0 0 0 0 4.5C0 8 4.5 12 4.5 12S9 8 9 4.5A4.5 4.5 0 0 0 4.5 0z" fill="#777"/></svg>Hallstead, LV &nbsp;&nbsp;|&nbsp;&nbsp;<svg width="11" height="11" viewBox="0 0 11 11" fill="none" stroke="#777"><circle cx="5.5" cy="5.5" r="4.8"/><path d="M5.5 2.5v3h2"/></svg>Full/Part-time</div>
  <div class="btn">APPLY NOW</div>
</div>

<!-- PARTNERS -->
<h2 class="section-title" style="top:3028px">OUR PARTNERS</h2>
<svg class="abs" style="left:36px;top:3132px" width="16" height="28" viewBox="0 0 16 28" fill="none" stroke="#aaa" stroke-width="2.5"><path d="M14 2L3 14l11 12"/></svg>
<svg class="abs" style="left:1154px;top:3132px" width="16" height="28" viewBox="0 0 16 28" fill="none" stroke="#aaa" stroke-width="2.5"><path d="M2 2l11 12L2 26"/></svg>
<div class="partner" style="left:90px"><i></i>Norvalis</div>
<div class="partner" style="left:270px"><i></i>Quentara</div>
<div class="partner" style="left:480px"><i></i>Pellimo</div>
<div class="partner" style="left:650px"><i></i>Banca Orvesta</div>
<div class="partner" style="left:848px"><i></i>Bank Kalmiro</div>
<div class="partner" style="left:1040px"><i></i>Tressandi</div>

<!-- CONTACT -->
<section class="contact">
  <h2 class="section-title" style="top:48px">CONTACT US</h2>
</section>
<div class="form-box"></div>
<div class="field" style="left:218px;top:3411px;width:204px">Name</div>
<div class="field" style="left:448px;top:3411px;width:202px">E mail</div>
<div class="field" style="left:218px;top:3477px;width:204px">Phone</div>
<div class="field" style="left:448px;top:3477px;width:202px">Subject</div>
<div class="abs" style="left:220px;top:3540px;width:429px;height:157px;border:1px solid #888;font-size:12px;padding:22px 20px">Message</div>
<div class="btn" style="left:222px;top:3727px;width:119px;height:41px;font-size:17px;box-shadow:none">SUBMIT</div>

<div class="info-box">
  <div class="info-ic" style="top:76px"><svg width="38" height="38" viewBox="0 0 38 38"><path d="M19 11a6 6 0 0 0-6 6c0 5 6 11 6 11s6-6 6-11a6 6 0 0 0-6-6z" fill="#fff"/><circle cx="19" cy="17" r="2.2" fill="#2f8ee0"/></svg></div>
  <p class="info-h" style="top:83px">ADDRESS</p>
  <p class="info-t" style="top:111px">47 Lindenweg Court<br>Harrow Bend, 20419</p>
  <div class="info-rule" style="top:185px"></div>
  <div class="info-ic" style="top:207px"><svg width="38" height="38" viewBox="0 0 38 38"><path d="M14 11l4 4-2 3c1 2 3 4 5 5l3-2 4 4-3 3c-6 0-14-8-14-14z" fill="#fff"/></svg></div>
  <p class="info-h" style="top:209px">TELEPHONE</p>
  <p class="info-t" style="top:230px">555.010.2040</p>
  <div class="info-rule" style="top:276px"></div>
  <div class="info-ic" style="top:309px"><svg width="38" height="38" viewBox="0 0 38 38"><rect x="11" y="13" width="16" height="12" rx="1" fill="#fff"/><path d="M11 14l8 6 8-6" stroke="#2f8ee0" stroke-width="1.5" fill="none"/></svg></div>
  <p class="info-h" style="top:311px">E MAIL US</p>
  <p class="info-t" style="top:332px">info@velmatrix.com</p>
</div>

<!-- FOOTER -->
<footer class="footer">
  <div class="abs" style="left:166px;top:122px;font-family:'Poppins',sans-serif;font-weight:700;font-size:38px;color:var(--white)">VelmaTrix</div>
  <p class="f-h" style="left:475px">CONTACT US</p>
  <div class="f-in" style="top:70px;height:28px">NAME</div>
  <div class="f-in" style="top:108px;height:30px">E MAIL</div>
  <div class="f-in" style="top:144px;height:64px">MESSAGE</div>
  <div class="btn" style="left:475px;top:212px;width:228px;height:42px;font-size:18px;box-shadow:none">SUBMIT</div>
  <p class="f-h" style="left:775px">MENU</p>
  <div class="f-menu">Home<br>Services<br>Partner<br>Contact Us<br>Karriere<br>Über Uns<br>Kontakt</div>
  <p class="f-h" style="left:960px">CONNECT WITH US</p>
  <div class="soc" style="top:78px"><span></span>Friendnet</div>
  <div class="soc" style="top:118px"><span></span>Chirpline</div>
  <div class="soc" style="top:158px"><span></span>Workfolk</div>
  <div class="abs" style="left:144px;top:320px;width:910px;height:1px;background:rgba(255,255,255,.35)"></div>
  <p class="abs" style="left:0;top:360px;width:1200px;text-align:center;font-size:11px;color:var(--white)">Copyrights @ 2019 All Rights Reserved</p>
</footer>

</body>
</html>
```